Plakat-Design für Bausparen und Versicherungen
Zielgruppe
Baufinanzierung, Anschlußfinanzierung,Privatkredite, Bausparen und Versicherungen
also jedes Prtodukt muss einzeln aber im klieinen sollte auf unser Produkte hingewiesen werden. Es muß aAbmahnsicher sein beim Zins muß noch ein Sternchen hin und in ganz klein mit erwähnt werden.
wir haben uns schon ein paar Gedanken gemacht, also Einfach mehr Freiheit sollte es schon sein als Spruch.
Falls das Logo von uns noch extra benötigt wird, bitte anfordern.
Aufgabenstellung
Sexy, auffallend, erfrischend anders als der Markt z.B.: Quarzeno und Dr Wendt

```html
<!DOCTYPE html>
<html lang="de">
<head>
<meta charset="utf-8">
<title>Neues Auto – fondwerk Plakat</title>
<link href="https://fonts.googleapis.com/css2?family=Quicksand:wght@400;500;600;700&display=swap" rel="stylesheet">
<style>
  :root {
    --brand-blue: #22448a;
    --footer-blue: #1f3f86;
    --accent-start: #e85a52;
    --accent-end: #e8602a;
    --white: #ffffff;
    --ink-orange: #e4602f;
    --footnote: #c9d2e6;
  }
  * { margin: 0; padding: 0; box-sizing: border-box; }
  html, body { width: 848px; height: 1200px; overflow: hidden; background: var(--white); }
  .poster {
    position: relative;
    width: 848px; height: 1200px;
    overflow: hidden;
    background: var(--white);
    font-family: "Quicksand", sans-serif;
  }
  .hero-photo {
    position: absolute; left: 0; top: 0;
    width: 848px; height: 690px;
    background: linear-gradient(180deg, #4d5b69 0%, #7b8792 22%, #a3abb0 38%, #51683f 44%, #6f7a5c 52%, #4f6a7a 62%, #3d5d6c 75%, #8b8c84 86%, #9a9a92 100%);
    clip-path: polygon(0 0, 100% 0, 100% 655px, 0 684px);
  }
  .headline {
    position: absolute; top: 18px; left: 0; width: 100%;
    text-align: center;
    color: var(--white);
    font-size: 72px; font-weight: 600; letter-spacing: 1px;
  }
  .offer-burst {
    position: absolute; left: 603px; top: 583px;
    width: 230px; height: 230px;
  }
  .offer-text {
    position: absolute; left: 603px; top: 670px; width: 230px;
    text-align: center; color: var(--white);
  }
  .offer-title { font-size: 28px; font-weight: 700; line-height: 1; }
  .offer-rate { font-size: 14px; font-weight: 600; margin-top: 8px; }
  .brand-name {
    position: absolute; top: 720px; left: 0; width: 100%;
    text-align: center;
    color: var(--brand-blue);
    font-size: 36px; font-weight: 500; letter-spacing: 0.5px;
  }
  .brand-slogan {
    position: absolute; top: 776px; left: 0; width: 100%;
    text-align: center;
    color: var(--ink-orange);
    font-size: 21px; font-weight: 600;
  }
  .products {
    position: absolute; top: 833px; left: 0; width: 100%;
    list-style: none;
  }
  .product {
    position: absolute; top: 0; width: 200px; margin-left: -100px;
    text-align: center;
  }
  .product-tile {
    width: 101px; height: 101px; margin: 0 auto;
    background: var(--brand-blue);
    border-radius: 4px;
    box-shadow: 1px 2px 3px rgba(0,0,0,0.25);
    display: flex; align-items: center; justify-content: center;
  }
  .product-tile svg { width: 60px; height: 60px; fill: var(--white); }
  .product-label {
    margin-top: 14px;
    color: var(--brand-blue);
    font-size: 14px; font-weight: 500; letter-spacing: 0.3px;
    white-space: nowrap;
  }
  .cta {
    position: absolute; left: 295px; top: 993px;
    width: 258px; height: 69px;
    background: linear-gradient(90deg, var(--accent-start), var(--accent-end));
    box-shadow: 1px 2px 3px rgba(0,0,0,0.25);
    display: flex; align-items: center; justify-content: center;
    color: var(--white); font-size: 26px; font-weight: 700;
  }
  .contact-band {
    position: absolute; left: 0; top: 1070px; width: 848px; height: 130px;
    background: var(--footer-blue);
    clip-path: polygon(0 35px, 100% 6px, 100% 100%, 0 100%);
  }
  .contact-row { position: absolute; font-size: 11.5px; font-weight: 600; color: var(--white); line-height: 20px; }
  .contact-label { left: 166px; top: 1113px; color: var(--ink-orange); }
  .contact-person { left: 298px; top: 1113px; }
  .contact-reach { left: 568px; top: 1113px; }
  .footnote {
    position: absolute; top: 1180px; left: 0; width: 100%;
    text-align: center; color: var(--footnote);
    font-size: 8.5px; font-weight: 400;
  }
</style>
</head>
<body>
<main class="poster">
  <div class="hero-photo" role="img" aria-label="Foto: türkisfarbenes Sportcoupé von hinten auf einer Landstraße unter grauem Himmel, Felder und Bäume im Hintergrund"></div>
  <h1 class="headline">NEUES AUTO</h1>

  <svg class="offer-burst" viewBox="-100 -100 200 200" aria-hidden="true">
    <defs>
      <linearGradient id="burstFill" x1="0" y1="0" x2="1" y2="1">
        <stop offset="0" stop-color="#e85a52"/>
        <stop offset="1" stop-color="#e8602a"/>
      </linearGradient>
    </defs>
    <polygon transform="rotate(8)" fill="url(#burstFill)" points="0,-100 15,-56 50,-87 41,-41 87,-50 56,-15 100,0 56,15 87,50 41,41 50,87 15,56 0,100 -15,56 -50,87 -41,41 -87,50 -56,15 -100,0 -56,-15 -87,-50 -41,-41 -50,-87 -15,-56"/>
  </svg>
  <div class="offer-text">
    <div class="offer-title">Kredite</div>
    <div class="offer-rate">ab 0,9%*</div>
  </div>

  <div class="brand-name">fondwerk</div>
  <p class="brand-slogan">Klar finanziert mit Konzept</p>

  <ul class="products">
    <li class="product" style="left:77px">
      <div class="product-tile">
        <svg viewBox="0 0 60 60"><path d="M30 8 L4 30 L9 34 L14 30 V50 H25 V38 H35 V50 H46 V30 L51 34 L56 30 L45 20.6 V11 H40 V16.4 Z"/></svg>
      </div>
      <div class="product-label">BAUFINANZIERUNG</div>
    </li>
    <li class="product" style="left:250px">
      <div class="product-tile">
        <svg viewBox="0 0 60 60"><text x="30" y="30" text-anchor="middle" font-family="Quicksand, sans-serif" font-weight="700" font-size="28" fill="#fff">$</text><path d="M6 46 H22 L34 44 C38 43 40 40 37 38 L28 40 H22 L36 36 L48 30 C52 28 56 32 52 35 L38 46 C35 48 32 50 28 50 H6 Z"/></svg>
      </div>
      <div class="product-label">PRIVATKREDITE</div>
    </li>
    <li class="product" style="left:424px">
      <div class="product-tile">
        <svg viewBox="0 0 60 60"><path fill-rule="evenodd" d="M2 16 H58 V44 H2 Z M7 21 V27 L13 21 Z M53 21 H47 L53 27 Z M7 39 V33 L13 39 Z M53 39 H47 L53 33 Z M30 20 A10 10 0 1 0 30.01 20 Z"/><text x="30" y="35" text-anchor="middle" font-family="Quicksand, sans-serif" font-weight="700" font-size="14" fill="#22448a">1</text></svg>
      </div>
      <div class="product-label">ANSCHLUSSFINANZIERUNG</div>
    </li>
    <li class="product" style="left:597px">
      <div class="product-tile">
        <svg viewBox="0 0 60 60"><path d="M22 18 A6 6 0 0 1 34 18 Z"/><path d="M12 32 C12 24 20 20 30 20 C38 20 44 23 46 26 L50 22 V30 L54 32 V38 L48 40 C47 42 46 43 44 44 V52 H38 V47 H24 V52 H18 V44 C14 42 12 38 12 34 C8 34 6 32 7 29 L9 29 C9 31 10 32 12 32 Z"/></svg>
      </div>
      <div class="product-label">BAUSPAREN</div>
    </li>
    <li class="product" style="left:771px">
      <div class="product-tile">
        <svg viewBox="0 0 60 60"><path fill-rule="evenodd" d="M18 28 V20 A12 12 0 0 1 42 20 V28 H46 C48 28 50 30 50 32 V50 C50 52 48 54 46 54 H14 C12 54 10 52 10 50 V32 C10 30 12 28 14 28 Z M24 28 H36 V20 A6 6 0 0 0 24 20 Z"/></svg>
      </div>
      <div class="product-label">VERSICHERUNGEN</div>
    </li>
  </ul>

  <a class="cta">www.fondwerk.de</a>

  <footer>
    <div class="contact-band"></div>
    <div class="contact-row contact-label">Ihr Ansprechpartner</div>
    <div class="contact-row contact-person">Jonas Hartwig<br>Lindenweg 9b, 23560 Lübeck</div>
    <div class="contact-row contact-reach">04521 5 8827310<br>jonas.hartwig@fondwerk.de</div>
    <p class="footnote">* Lorem ipsum dolor sit amet, consetetur sadipscing elitr, sed diam nonumy.</p>
  </footer>
</main>
</body>
</html>
```